Landing Page - #1 Social Media Training

I need a landing page where i'm going to sell the number one social media for small business package. Hopefully i can use this template for others.

The themes are in oranges.

See www.quvendrip.com

Its a dogs breakfast.

I need high end, good looking, zelo/paybridgex/logos.
Would love a wordpress design but i could slice it into one if it wasn't.

Need room for feature bullet points, a video preview, and text along the bottom... Want it in oranges and whites like the packaging with social media along the top... Side bar on the right for opt-in box, left side copy etc.

Target Market(s)

The audience is small and medium businesses.

Industry/Entity Type

Small Business

Requirements
Must have
• Opt-in
headline
footer

```html
<!DOCTYPE html>
<html lang="en">
<head>
<meta charset="utf-8">
<title>Trail Start 101 – Social Media &amp; Internet Marketing</title>
<link href="https://fonts.googleapis.com/css2?family=Source+Sans+3:wght@400;600&family=Caveat:wght@400&display=swap" rel="stylesheet">
<style>
  :root{
    --orange:#f4861f;
    --orange-light:#ffa10a;
    --dark:#1e1e1e;
    --dark-mid:#3b3b3b;
    --green:#7cb518;
    --blue:#4f8fcc;
    --ink:#1b1b1b;
    --text-dark:#333333;
    --field:#f3f3f3;
    --white:#ffffff;
  }
  *{margin:0;padding:0;box-sizing:border-box}
  html,body{width:1000px;height:1200px;overflow:hidden}
  body{font-family:"Source Sans 3",Arial,sans-serif;color:var(--ink);background:var(--white);position:relative}

  .hero{position:absolute;left:0;top:0;width:1000px;height:490px;background:linear-gradient(180deg,var(--dark) 0%,var(--dark-mid) 100%);overflow:hidden}
  .hero-band{position:absolute;left:0;top:0}
  .brand{position:absolute;left:38px;top:22px;font-size:62px;font-weight:600;color:var(--orange);letter-spacing:1px;line-height:1}
  .product-title{position:absolute;right:22px;top:8px;font-family:"Caveat",cursive;font-size:50px;color:var(--orange);line-height:1}
  .author{position:absolute;right:32px;top:68px;font-size:18px;color:var(--white)}

  .package{position:absolute;left:95px;top:138px;width:295px;height:298px;background:linear-gradient(135deg,#ffffff 0%,#e9e9e9 60%,#f4f4f4 100%);border-radius:2px}
  .buy-badge{position:absolute;left:202px;top:362px;width:118px;height:118px;border-radius:50%;background:radial-gradient(circle at 40% 35%,#ffffff 0%,#cfcfcf 70%,#9a9a9a 100%);display:flex;align-items:center;justify-content:center;flex-direction:column;font-family:Georgia,serif;font-size:24px;line-height:1;color:#111;transform:rotate(18deg)}
  .price-tag{position:absolute;left:400px;top:116px}
  .price{position:absolute;left:410px;top:326px;width:76px;text-align:center;font-size:26px;font-weight:600;color:#111}
  .price-note{position:absolute;left:406px;top:360px;width:84px;text-align:center;font-size:8px;color:#111}

  .pitch{position:absolute;left:460px;width:530px;text-align:center}
  .pitch-kicker{top:186px;font-size:24px;color:var(--white)}
  .pitch-headline{top:228px;font-size:33px;color:var(--text-dark)}
  .pitch-offer{top:290px;font-size:24px;color:var(--blue);line-height:29px;left:470px;width:500px}
  .pitch-includes{top:362px;font-size:16px;color:#111;left:500px;width:465px}

  .content{position:absolute;left:0;top:490px;width:1000px;height:638px;background:linear-gradient(180deg,#e4e4e4 0%,#ffffff 60%)}
  .section-title{position:absolute;font-size:23px;color:var(--green);line-height:29px}
  .intro{left:97px;top:54px}
  .features{position:absolute;left:97px;top:128px;list-style:none}
  .features li{position:relative;padding-left:39px;height:38.5px;font-size:15px}
  .features li::before{content:"";position:absolute;left:0;top:9px;width:3px;height:3px;border-radius:50%;background:#111}
  .payment-title{left:97px;top:407px}
  .cards{position:absolute;left:93px;top:451px;display:flex;gap:3px}
  .card{height:25px;border:1px solid #b9b9b9;background:#fafafa;font-size:11px;font-weight:600;color:var(--text-dark);display:flex;align-items:center;justify-content:center;width:46px}
  .card.wide{width:66px}
  .connect-title{left:96px;top:493px}
  .social{position:absolute;left:96px;top:536px;display:flex;gap:8px}
  .social span{width:28px;height:28px;border-radius:50%;background:radial-gradient(circle at 40% 35%,#fafafa,#b5b5b5)}

  .video-title{position:absolute;left:468px;top:36px;font-size:23px;color:var(--orange)}
  .player{position:absolute;left:459px;top:77px;width:457px;height:308px;border-radius:8px;background:linear-gradient(180deg,#2a2a2a,#111)}
  .screen{position:absolute;left:10px;top:11px;width:435px;height:260px;border-radius:8px;background:linear-gradient(100deg,#6c6560 0%,#bdbab6 45%,#e9e8ea 100%)}
  .play{position:absolute;left:202px;top:104px;width:74px;height:50px;border-radius:10px;background:rgba(20,20,20,.75)}
  .play::after{content:"";position:absolute;left:29px;top:14px;border-left:22px solid #fff;border-top:11px solid transparent;border-bottom:11px solid transparent}
  .progress{position:absolute;left:12px;top:282px;width:371px;height:4px;background:#3c3c3c}
  .progress::before{content:"";position:absolute;left:0;top:0;width:35px;height:4px;background:var(--green)}
  .ctrl{position:absolute;top:277px;width:18px;height:18px;border-radius:50%;background:#3a3a3a}
  .ctrl.play-btn{left:395px}
  .ctrl.play-btn::after{content:"";position:absolute;left:6px;top:4px;border-left:8px solid var(--green);border-top:5px solid transparent;border-bottom:5px solid transparent}
  .ctrl.pause-btn{left:416px}
  .ctrl.pause-btn::after{content:"";position:absolute;left:5px;top:5px;width:8px;height:8px;border-left:3px solid var(--green);border-right:3px solid var(--green)}

  .optin{position:absolute;left:452px;top:404px;width:464px;height:206px;border-radius:8px;background:var(--orange)}
  .optin label{position:absolute;left:37px;font-size:15px;font-weight:600;color:#1a1a1a}
  .optin .field{position:absolute;left:124px;width:321px;height:27px;background:var(--field);border:none}
  .optin textarea.field{height:63px;resize:none}
  .submit{position:absolute;left:223px;top:169px;width:98px;height:30px;border-radius:10px;border:none;background:linear-gradient(180deg,#3c3c3c,#0d0d0d);color:var(--white);font-family:inherit;font-size:15px}

  .footer{position:absolute;left:0;top:1128px;width:1000px;height:72px;background:linear-gradient(180deg,#2b2b2b,#3d3d3d);color:var(--white);text-align:center;font-size:12px;line-height:14px;padding-top:18px}
</style>
</head>
<body>
  <header class="hero">
    <svg class="hero-band" width="1000" height="490" viewBox="0 0 1000 490" aria-hidden="true">
      <defs>
        <linearGradient id="bandFill" x1="0" y1="0" x2="0" y2="1">
          <stop offset="0" stop-color="#ffa10a"/>
          <stop offset="1" stop-color="#f4861f"/>
        </linearGradient>
      </defs>
      <polygon points="612,110 1000,110 1000,490 0,490 0,472" fill="url(#bandFill)"/>
    </svg>
    <div class="brand">Lumio</div>
    <div class="product-title">Trail Start 101</div>
    <div class="author">Dale Morrow</div>

    <div class="package" role="img" aria-label="Trail Start 101 DVD package boxes"></div>
    <div class="buy-badge"><span>BUY</span><span>Now</span></div>

    <svg class="price-tag" width="100" height="270" viewBox="0 0 100 270" aria-hidden="true">
      <circle cx="43" cy="6" r="4" fill="#ddd"/>
      <line x1="43" y1="6" x2="45" y2="188" stroke="#eee" stroke-width="1.5"/>
      <path d="M28 178 H62 L88 210 V262 H6 V210 Z" fill="#f1f1f1" stroke="#d6d6d6"/>
      <circle cx="45" cy="192" r="3" fill="#bbb"/>
    </svg>
    <div class="price">$499</div>
    <div class="price-note">Plus Sales tax &amp; Shipping</div>

    <p class="pitch pitch-kicker">Social Media &amp; Internet Marketing</p>
    <h1 class="pitch pitch-headline" style="font-weight:400">for Today’s Small to Medium Business</h1>
    <p class="pitch pitch-offer">All of this information is<br>FREE to extremely LOW COST</p>
    <p class="pitch pitch-includes">Includes: 4 DVDs &amp; a Step-by-Step “Do It Yourself” Workbook</p>
  </header>

  <main class="content">
    <h2 class="section-title intro" style="font-weight:400">One easy system to help<br>grow your business online!</h2>
    <ul class="features">
      <li>Search Engine Marketing</li>
      <li>Social Media Marketing</li>
      <li>Social Network Marketing</li>
      <li>Internet Marketing</li>
      <li>Applications</li>
      <li>Social Tools</li>
      <li>Community Development</li>
    </ul>

    <h2 class="section-title payment-title" style="font-weight:400">Payment</h2>
    <div class="cards">
      <span class="card">zelo</span>
      <span class="card">Amplo</span>
      <span class="card" style="font-size:8px">paybridgex</span>
      <span class="card wide">Coinvale</span>
    </div>

    <h2 class="section-title connect-title" style="font-weight:400">Connect with us</h2>
    <div class="social" aria-label="Social links">
      <span></span><span></span><span></span><span></span>
    </div>

    <h2 class="video-title" style="font-weight:400">Video</h2>
    <div class="player">
      <div class="screen" role="img" aria-label="Video preview of a presenter explaining an online store tool"></div>
      <div class="play" style="left:212px;top:115px"></div>
      <div class="progress"></div>
      <div class="ctrl play-btn"></div>
      <div class="ctrl pause-btn"></div>
    </div>

    <form class="optin">
      <label style="top:27px">Username</label>
      <input class="field" type="text" style="top:20px">
      <label style="top:63px">Password</label>
      <input class="field" type="password" style="top:58px">
      <label style="top:99px">Message</label>
      <textarea class="field" style="top:97px"></textarea>
      <button class="submit" type="button">Submit</button>
    </form>
  </main>

  <footer class="footer">
    Copyright © 2011<br>Terms and Conditions - Privacy Policy
  </footer>
</body>
</html>
```